The Lantern Guild Pitchdeck Template

The Lantern Guild would like a branded pitch deck template design for members to use when presenting their projects and proposals. The deck should include 10-15 different slide designs, each with the same branded theme, but with a variety of icon graphics and other design features that will empower members to easily create a beautiful pitch deck just by adding written content.

Please visit lanternguildhq.org to get a sense for our branding - purple, space, galaxy, white font and the planetary logo are some commonalities.

Here are 2 google drive links with some additional designs

https://files.boxmeadow.net/share/f/8QzrTa2Lk5VbNw7cHyP0dJe3sUmXg4RiF

https://files.boxmeadow.net/share/f/3Kd9-Rm6Tq2-yLvBn051fopwxhcT_zj7

```html
<!DOCTYPE html>
<html lang="en">
<head>
<meta charset="utf-8">
<title>The Lantern Guild – Pitch Deck Template</title>
<link href="https://fonts.googleapis.com/css2?family=Cabin:wght@400;500;600&display=swap" rel="stylesheet">
<style>
:root{
  --stage:#d5c9dd;
  --navy:#101a33;
  --indigo:#262067;
  --violet:#3b2a8a;
  --lilac:#c9c3de;
  --grey:#e9e9ec;
  --ink:#1c2238;
  --white:#ffffff;
  --galaxy:radial-gradient(circle at 42% 45%,#7d63d0 0,#3b2a8a 35%,#17123f 75%);
  --nebula:linear-gradient(90deg,#1d3a66,#6f9cc8 45%,#c9dced 50%,#5f86b6 55%,#1d3358);
  --sun:radial-gradient(circle at 55% 45%,#f4b25a 0,#c45d22 40%,#3a1a0c 80%);
  --rock:linear-gradient(135deg,#2f4d6a,#6a8aa4 45%,#23364b 70%,#4f6e88);
  --dunes:linear-gradient(180deg,#5a2c8e,#b46ac8 45%,#7a4aa8 70%,#3a2360);
  --dusk:linear-gradient(180deg,#4a3060,#c86672 40%,#e39a86 55%,#3b2433);
  --eye:linear-gradient(135deg,#2b1d18,#5a4a52 40%,#5c7590 55%,#3a2a24 85%);
  --deepspace:linear-gradient(135deg,#0c1330,#24307a 45%,#8a5ab8 60%,#1b2a6a 85%);
  --peak:linear-gradient(180deg,#c4b4cf,#6c5a74 35%,#2f2838 55%,#d2a79e 80%,#b98f8b);
  --cliff:linear-gradient(135deg,#a8aab8,#59566a 40%,#8d62c0 65%,#3a3448);
  --spiral:linear-gradient(160deg,#3d74c0,#13234f 55%,#070c1e);
  --cloud:linear-gradient(180deg,#101a38,#6a3aa8 40%,#e06ac0 60%,#101a38);
}
*{box-sizing:border-box;margin:0;padding:0}
html,body{width:1200px;height:890px;overflow:hidden;background:var(--stage);font-family:"Cabin",sans-serif;color:var(--ink)}
.deck{position:relative;width:1200px;height:890px}
.slide{position:absolute;width:182px;height:102px;background:var(--white);overflow:hidden;box-shadow:0 1px 2px rgba(40,30,60,.18)}
.dark{background:var(--navy);color:var(--white)}
.photo{position:absolute}
.title{position:absolute;font-size:4.6px;font-weight:400;letter-spacing:.15px;text-transform:uppercase;line-height:1.1}
.lead{position:absolute;font-size:2.9px;text-transform:uppercase;line-height:1.25}
.body{position:absolute;font-size:1.7px;line-height:1.35}
.light{color:var(--white)}
.mark{position:absolute;right:5px;bottom:4px;font-size:2px;letter-spacing:.1px}
.abs{position:absolute}
.row{display:flex}
</style>
</head>
<body>
<main class="deck">

<!-- row 1 -->
<section class="slide dark" style="left:52px;top:110px">
  <div class="photo" style="left:0;top:0;width:122px;height:102px;background:var(--galaxy)" role="img" aria-label="Purple starfield wave behind a figure"></div>
  <div class="abs light" style="left:0;top:44px;width:122px;text-align:center;font-size:6px;letter-spacing:1px;font-weight:500">The Lantern Guild</div>
  <h1 class="title" style="left:126px;top:22px;font-size:5.6px">Business<br>Summary</h1>
  <p class="lead" style="left:126px;top:44px;width:52px">Lorem ipsum dolor sit amet, consectetuer adipiscing elit, sed di</p>
</section>

<section class="slide" style="left:281px;top:110px">
  <div class="photo" style="left:0;top:0;width:182px;height:62px;background:var(--nebula)" role="img" aria-label="Blue nebula seen through a dome"></div>
  <h2 class="title light" style="left:8px;top:5px;font-size:3.6px">Graphic 02</h2>
  <svg class="abs" style="left:0;top:52px" width="182" height="50">
    <g font-size="1.6" fill="#fff" text-anchor="middle">
      <circle cx="25" cy="10" r="5.5" fill="#101a33"/><text x="25" y="10.6">2014</text>
      <circle cx="57" cy="10" r="5.5" fill="#1e3f7a"/><text x="57" y="10.6">2015</text>
      <circle cx="89" cy="10" r="5.5" fill="#101a33"/><text x="89" y="10.6">2016</text>
      <circle cx="121" cy="10" r="5.5" fill="#1e3f7a"/><text x="121" y="10.6">2017</text>
      <circle cx="153" cy="10" r="5.5" fill="#101a33"/><text x="153" y="10.6">2018</text>
    </g>
    <g font-size="1.9" fill="#1c2238" text-anchor="middle">
      <text x="25" y="20">Project One</text><text x="57" y="20">Project Two</text><text x="89" y="20">Project Three</text><text x="121" y="20">Project Four</text><text x="153" y="20">Project Five</text>
      <text x="25" y="27">Marketers</text><text x="57" y="27">Marketers</text><text x="89" y="27">Marketers</text><text x="121" y="27">Marketers</text><text x="153" y="27">Marketers</text>
    </g>
    <g font-size="1.3" fill="#555" text-anchor="middle">
      <text x="25" y="32">Teams learn the life</text><text x="25" y="34">cycle of a product</text>
      <text x="57" y="32">Teams learn the life</text><text x="57" y="34">cycle of a product</text>
      <text x="89" y="32">Teams learn the life</text><text x="89" y="34">cycle of a product</text>
      <text x="121" y="32">Teams learn the life</text><text x="121" y="34">cycle of a product</text>
      <text x="153" y="32">Teams learn the life</text><text x="153" y="34">cycle of a product</text>
    </g>
  </svg>
  <span class="mark">The Lantern Guild</span>
</section>

<section class="slide dark" style="left:504px;top:110px">
  <h2 class="title" style="left:9px;top:5px;font-size:3.6px">Images</h2>
  <div class="photo" style="left:11px;top:18px;width:40px;height:40px;border-radius:50%;background:var(--dunes)" role="img" aria-label="Glowing planet over dunes"></div>
  <div class="photo" style="left:83px;top:2px;width:44px;height:44px;border-radius:50%;background:linear-gradient(#c8d4e2,#3c6c9e)" role="img" aria-label="Bird over ocean with brand name"></div>
  <div class="abs light" style="left:83px;top:22px;width:44px;text-align:center;font-size:2.6px">The Lantern Guild</div>
  <div class="photo" style="left:65px;top:54px;width:40px;height:40px;border-radius:50%;background:linear-gradient(#241b5a,#6a5a9a 50%,#e0a8b8)" role="img" aria-label="Planets above a mountain"></div>
  <p class="lead" style="left:130px;top:22px;font-size:1.9px">Lorem ipsum dolor sit amet.</p>
  <p class="body" style="left:130px;top:27px;width:44px">Short notes on the plan go here with goals, dates and a clear outcome that the team will share at review.</p>
  <p class="lead" style="left:9px;top:64px;font-size:1.9px">Lorem ipsum dolor sit amet.</p>
  <p class="body" style="left:9px;top:69px;width:48px">Short notes on the plan go here with goals, dates and a clear outcome that the team will share at review.</p>
  <p class="lead" style="left:118px;top:70px;font-size:1.9px">Lorem ipsum dolor sit amet.</p>
  <p class="body" style="left:118px;top:75px;width:48px">Short notes on the plan go here with goals, dates and a clear outcome that the team will share at review.</p>
  <span class="mark">The Lantern Guild</span>
</section>

<section class="slide" style="left:718px;top:110px">
  <div class="photo" style="inset:0;background:var(--rock)" role="img" aria-label="Cracked blue rock revealing stars"></div>
  <div class="abs dark" style="left:100px;top:0;width:65px;height:60px"></div>
  <p class="lead light" style="left:108px;top:21px;width:50px;font-size:1.9px">Lorem ipsum dolor sit amet.</p>
  <p class="body light" style="left:108px;top:28px;width:50px">Short notes on the plan go here with goals, dates and a clear outcome that the team will share at review.</p>
  <span class="mark light">The Lantern Guild</span>
</section>

<section class="slide" style="left:952px;top:110px">
  <div class="photo" style="inset:0;background:var(--dunes)" role="img" aria-label="Figure walking on purple dunes under a galaxy"></div>
  <p class="lead light" style="left:9px;top:17px;width:68px;font-size:3.8px;line-height:1.2">Lorem ipsum dolor sit amet, consectetuer adipiscing elit, sed diam nonummy nibh euismod tincidunt ut laoreet dolore magna aliquam erat volutpat. Ut wisi enim ad minim veniam, quis</p>
  <span class="mark light">The Lantern Guild</span>
</section>

<!-- row 2 -->
<section class="slide" style="left:52px;top:256px">
  <div class="photo" style="left:0;top:0;width:110px;height:102px;background:var(--sun)" role="img" aria-label="Figure before a burning orange star"></div>
  <h2 class="title light" style="left:8px;top:5px;font-size:3.6px">Agenda</h2>
  <ol class="abs" style="left:114px;top:22px;list-style:none;font-size:2.2px;line-height:1.6;text-transform:uppercase">
    <li>02 &nbsp;Vision</li><li>03 &nbsp;About</li><li>04 &nbsp;Our team</li><li>05 &nbsp;Summary</li><li>06 &nbsp;Vision</li><li>07 &nbsp;About</li><li>08 &nbsp;Our team</li><li>09 &nbsp;Summary</li><li>10 &nbsp;Vision</li><li>11 &nbsp;About</li><li>12 &nbsp;Our team</li><li>13 &nbsp;Summary</li>
  </ol>
  <p class="lead" style="left:114px;top:78px;width:62px;font-size:1.6px">Lorem ipsum dolor sit amet, consectetuer adipiscing elit, sed diam nonummy nibh euismod tincidunt ut laoreet dolore magna aliquam erat volutpat.</p>
  <span class="mark">The Lantern Guild</span>
</section>

<section class="slide" style="left:281px;top:256px">
  <h2 class="title" style="left:9px;top:5px;font-size:3.6px">Checkmark</h2>
  <p class="body" style="left:9px;top:11px;width:64px">Short notes on the plan go here with goals, dates and a clear outcome that the team will share at review. Add key facts, the budget and the people who lead each part of the work.</p>
  <p class="body" style="left:9px;top:30px;width:64px">Short notes on the plan go here with goals, dates and a clear outcome that the team will share at review.</p>
  <div class="photo" style="left:73px;top:0;width:96px;height:49px;background:linear-gradient(135deg,#0c1a3a,#2f4f8a 55%,#0b1430)" role="img" aria-label="Glowing crystal cube above a hand"></div>
  <svg class="abs" style="left:0;top:49px" width="182" height="53">
    <polygon points="0,0 182,0 182,10 130,37 0,37" fill="#101a33"/>
    <g font-size="1.3" fill="#fff">
      <text x="9" y="9">To protect users,</text><text x="9" y="11">secure their data</text><text x="9" y="13">and keep trust.</text>
      <text x="35" y="9">To protect users,</text><text x="35" y="11">secure their data</text><text x="35" y="13">and keep trust.</text>
      <text x="61" y="9">To protect users,</text><text x="61" y="11">secure their data</text><text x="61" y="13">and keep trust.</text>
      <text x="87" y="9">To protect users,</text><text x="87" y="11">secure their data</text><text x="87" y="13">and keep trust.</text>
      <text x="113" y="9">To protect users,</text><text x="113" y="11">secure their data</text><text x="113" y="13">and keep trust.</text>
      <text x="139" y="9">To protect users,</text><text x="139" y="11">secure their data</text><text x="139" y="13">and keep trust.</text>
    </g>
  </svg>
  <span class="mark">The Lantern Guild</span>
</section>

<section class="slide dark" style="left:504px;top:256px">
  <div class="photo" style="inset:0;background:var(--sun);clip-path:polygon(0 0,100% 0,100% 38%,95% 52%,88% 60%,0 42%)" role="img" aria-label="Figure before an orange nebula"></div>
  <h2 class="title light" style="left:9px;top:5px;font-size:3.6px">About us 2</h2>
  <p class="lead" style="left:9px;top:62px;width:44px;font-size:2.1px">Lorem ipsum dolor sit amet, consectetuer adipiscing elit, sed diam nonummy nibh euismod tincidunt ut laoreet dolore magna</p>
  <p class="body" style="left:56px;top:62px;width:56px">Short notes on the plan go here with goals, dates and a clear outcome that the team will share at review. Add key facts, the budget and the people who lead each part of the work.</p>
  <span class="mark">The Lantern Guild</span>
</section>

<section class="slide" style="left:718px;top:256px">
  <div class="photo" style="inset:0;background:var(--deepspace);clip-path:polygon(0 0,72% 0,8% 100%,0 100%)" role="img" aria-label="Black hole in deep space"></div>
  <h2 class="title light" style="left:9px;top:5px;font-size:3.6px">Competencies</h2>
  <svg class="abs" style="left:0;top:0" width="182" height="102">
    <g fill="#101a33"><circle cx="113" cy="24" r="3"/><circle cx="93" cy="38" r="3"/><circle cx="77" cy="51" r="3"/><circle cx="58" cy="65" r="3"/><circle cx="39" cy="80" r="3"/></g>
    <g font-size="1.7" fill="#1c2238">
      <text x="119" y="23">LOREM IPSUM DOLOR SIT AMET,</text><text x="119" y="25.5">CONSECTETUER ADIPISCING ELIT.</text>
      <text x="99" y="37">LOREM IPSUM DOLOR SIT AMET,</text><text x="99" y="39.5">CONSECTETUER ADIPISCING ELIT.</text>
      <text x="83" y="50">LOREM IPSUM DOLOR SIT AMET,</text><text x="83" y="52.5">CONSECTETUER ADIPISCING ELIT.</text>
      <text x="64" y="64">LOREM IPSUM DOLOR SIT AMET,</text><text x="64" y="66.5">CONSECTETUER ADIPISCING ELIT.</text>
      <text x="45" y="79">LOREM IPSUM DOLOR SIT AMET,</text><text x="45" y="81.5">CONSECTETUER ADIPISCING ELIT.</text>
    </g>
  </svg>
  <span class="mark">The Lantern Guild</span>
</section>

<section class="slide" style="left:952px;top:256px">
  <div class="photo" style="left:0;top:0;width:121px;height:102px;background:var(--dusk)" role="img" aria-label="Ringed planet over a sunset shore"></div>
  <h2 class="title" style="left:125px;top:6px;width:52px;font-size:4px">Lorem ipsum dolor sit amet, consectetuer adipiscing elit, sed</h2>
  <p class="body" style="left:125px;top:33px;width:52px">Short notes on the plan go here with goals, dates and a clear outcome that the team will share at review. Add key facts, the budget and the people who lead each part of the work.</p>
  <span class="mark">The Lantern Guild</span>
</section>

<!-- row 3 -->
<section class="slide" style="left:52px;top:401px">
  <div class="abs" style="left:0;top:0;width:52px;height:102px;background:var(--indigo)"></div>
  <h2 class="title light" style="left:9px;top:5px;font-size:3.6px">Graphic 01</h2>
  <p class="lead light" style="left:9px;top:17px;width:42px;font-size:2px">Lorem ipsum dolor sit amet, consectetuer adipiscing elit, sed diam nonummy nibh euismod tincidunt ut laoreet dolore magna</p>
  <p class="body light" style="left:9px;top:42px;width:40px">Short notes on the plan go here with goals, dates and a clear outcome that the team will share at review. Add key facts and the budget.</p>
  <p class="body light" style="left:9px;top:74px;width:40px">Short notes on the plan go here with goals, dates and a clear outcome.</p>
  <svg class="abs" style="left:52px;top:0" width="130" height="102">
    <text x="55" y="34" font-size="2" text-anchor="middle" fill="#1c2238">Revenue Geo-Contribution</text>
    <g font-size="1.3" fill="#666" text-anchor="end">
      <text x="14" y="38">40.0%</text><text x="14" y="45">35.0%</text><text x="14" y="52">30.0%</text><text x="14" y="59">25.0%</text><text x="14" y="66">20.0%</text><text x="14" y="73">15.0%</text><text x="14" y="80">10.0%</text><text x="14" y="87">5.0%</text><text x="14" y="93">0.0%</text>
    </g>
    <g fill="#101a33">
      <rect x="25" y="45.5" width="6" height="47.5"/><rect x="55" y="48" width="6" height="45"/><rect x="85" y="67" width="6" height="26"/><rect x="114" y="74" width="6" height="19"/>
    </g>
    <g font-size="1.3" fill="#333" text-anchor="middle">
      <text x="28" y="44">34.75%</text><text x="58" y="46.5">32.47%</text><text x="88" y="65.5">18.69%</text><text x="117" y="72.5">13.90%</text>
      <text x="28" y="96">Emerging Market</text><text x="58" y="96">US</text><text x="88" y="96">Europe (incl UK)</text><text x="117" y="96">Established RoW</text>
    </g>
  </svg>
  <span class="mark" style="bottom:1.5px">The Lantern Guild</span>
</section>

<section class="slide" style="left:281px;top:401px">
  <h2 class="title" style="left:9px;top:5px;font-size:3.6px">Graphic 03</h2>
  <svg class="abs" style="left:0;top:0" width="112" height="102">
    <g font-size="1.7" fill="#555" text-anchor="middle"><text x="28" y="22">Sales</text><text x="81" y="22">Sales</text></g>
    <g transform="translate(28,42)">
      <circle r="18" fill="#a3a3a6"/>
      <path d="M0,0 L0,-18 A18,18 0 0 0 -17,6 Z" fill="#707074"/>
      <path d="M0,0 L-10,-15 A18,18 0 0 1 0,-18 Z" fill="#101a33"/>
      <path d="M0,0 L0,-18 A18,18 0 0 1 6,-17 Z" fill="#c9c3de"/>
    </g>
    <g transform="translate(81,42)">
      <circle r="18" fill="#a3a3a6"/>
      <path d="M0,0 L0,-18 A18,18 0 0 0 -17,6 Z" fill="#707074"/>
      <path d="M0,0 L-10,-15 A18,18 0 0 1 0,-18 Z" fill="#101a33"/>
      <path d="M0,0 L0,-18 A18,18 0 0 1 6,-17 Z" fill="#c9c3de"/>
    </g>
    <g font-size="1.2" fill="#555"><text x="12" y="66">● 1st Qtr  ● 2nd Qtr  ● 3rd Qtr  ● 4th Qtr</text><text x="65" y="66">● 1st Qtr  ● 2nd Qtr  ● 3rd Qtr  ● 4th Qtr</text></g>
  </svg>
  <p class="body" style="left:9px;top:74px;width:45px">Short notes on the plan go here with goals, dates and a clear outcome that the team will share at review.</p>
  <p class="body" style="left:61px;top:74px;width:45px">Short notes on the plan go here with goals, dates and a clear outcome that the team will share at review.</p>
  <div class="photo" style="left:112px;top:0;width:70px;height:102px;background:var(--dusk)" role="img" aria-label="Ringed planet over a dusk lake"></div>
  <span class="mark light">The Lantern Guild</span>
</section>

<section class="slide" style="left:504px;top:401px">
  <h2 class="title" style="left:9px;top:5px;font-size:3.6px">Table</h2>
  <p class="body" style="left:9px;top:11px;width:102px">Short notes on the plan go here with goals, dates and a clear outcome that the team will share at review. Add key facts, the budget and the people who lead each part of the work, plus the next steps and the main risks to watch.</p>
  <p class="body" style="left:9px;top:33px;width:102px">Short notes on the plan go here with goals, dates and a clear outcome.</p>
  <svg class="abs" style="left:9px;top:48px" width="104" height="46">
    <rect width="56" height="3" fill="#101a33"/><rect x="57" width="47" height="3" fill="#101a33"/>
    <g font-size="1.3" fill="#fff"><text x="3" y="2.2">BASE</text><text x="60" y="2.2">SCORE</text></g>
    <g fill="#e9e9ec"><rect y="4" width="104" height="3"/><rect y="12" width="104" height="3"/><rect y="20" width="104" height="3"/><rect y="28" width="104" height="3"/><rect y="36" width="104" height="3"/></g>
    <g font-size="1.3" fill="#1c2238">
      <text x="3" y="6.2">AVERAGE MONTHLY QUOTES</text><text x="60" y="6.2">432</text>
      <text x="3" y="10.2">AVERAGE MONTHLY QUOTES</text><text x="60" y="10.2">946</text>
      <text x="3" y="14.2">AVERAGE MONTHLY QUOTES</text><text x="60" y="14.2">350</text>
      <text x="3" y="18.2">AVERAGE MONTHLY QUOTES</text><text x="60" y="18.2">432</text>
      <text x="3" y="22.2">AVERAGE MONTHLY QUOTES</text><text x="60" y="22.2">946</text>
      <text x="3" y="26.2">AVERAGE MONTHLY QUOTES</text><text x="60" y="26.2">350</text>
      <text x="3" y="30.2">AVERAGE MONTHLY QUOTES</text><text x="60" y="30.2">946</text>
      <text x="3" y="34.2">AVERAGE MONTHLY QUOTES</text><text x="60" y="34.2">350</text>
    </g>
  </svg>
  <div class="photo" style="left:114px;top:0;width:68px;height:102px;background:var(--cloud)" role="img" aria-label="Tree shaped like a glowing pink nebula"></div>
  <span class="mark light">The Lantern Guild</span>
</section>

<section class="slide" style="left:718px;top:401px">
  <div class="photo" style="left:0;top:0;width:131px;height:102px;background:var(--peak)" role="img" aria-label="Figure on dunes before a dark mountain"></div>
  <h2 class="title light" style="left:9px;top:5px;font-size:3.6px">About us 2</h2>
  <p class="body" style="left:136px;top:20px;width:40px">Short notes on the plan go here with goals, dates and a clear outcome that the team will share at review. Add key facts and the budget.</p>
  <p class="body" style="left:136px;top:50px;width:40px">Short notes on the plan go here with goals, dates and a clear outcome that the team will share at review. Add key facts.</p>
  <span class="mark">The Lantern Guild</span>
</section>

<section class="slide" style="left:952px;top:401px">
  <div class="photo" style="left:0;top:0;width:154px;height:102px;background:var(--eye)" role="img" aria-label="Close-up eye reflecting an astronaut"></div>
  <div class="abs dark" style="left:123px;top:30px;width:59px;height:38px"></div>
  <p class="body light" style="left:127px;top:35px;width:51px">Short notes on the plan go here with goals, dates and a clear outcome that the team will share at review. Add key facts, the budget and the people who lead each part.</p>
  <span class="mark">The Lantern Guild</span>
</section>

<!-- row 4 -->
<section class="slide" style="left:52px;top:550px">
  <h2 class="title" style="left:9px;top:5px;font-size:3.6px">Our team</h2>
  <div class="abs" style="left:9px;top:14px;width:82px;display:grid;grid-template-columns:1fr 1fr;gap:20px 6px">
    <article><div class="row" style="gap:3px;align-items:center"><div style="width:7px;height:7px;background:#b9bccb" role="img" aria-label="Team member portrait"></div><p style="font-size:1.5px;line-height:1.3">ROWAN HALE<br>DIRECTOR</p></div><p style="font-size:1.4px;line-height:1.35;margin-top:2px">Short notes on this person, their role, past work and the skills they bring to the project team.</p></article>
    <article><div class="row" style="gap:3px;align-items:center"><div style="width:7px;height:7px;background:#b9bccb" role="img" aria-label="Team member portrait"></div><p style="font-size:1.5px;line-height:1.3">ROWAN HALE<br>DIRECTOR</p></div><p style="font-size:1.4px;line-height:1.35;margin-top:2px">Short notes on this person, their role, past work and the skills they bring to the project team.</p></article>
    <article><div class="row" style="gap:3px;align-items:center"><div style="width:7px;height:7px;background:#b9bccb" role="img" aria-label="Team member portrait"></div><p style="font-size:1.5px;line-height:1.3">ROWAN HALE<br>DIRECTOR</p></div><p style="font-size:1.4px;line-height:1.35;margin-top:2px">Short notes on this person, their role, past work and the skills they bring to the project team.</p></article>
    <article><div class="row" style="gap:3px;align-items:center"><div style="width:7px;height:7px;background:#b9bccb" role="img" aria-label="Team member portrait"></div><p style="font-size:1.5px;line-height:1.3">ROWAN HALE<br>DIRECTOR</p></div><p style="font-size:1.4px;line-height:1.35;margin-top:2px">Short notes on this person, their role, past work and the skills they bring to the project team.</p></article>
  </div>
  <div class="photo" style="left:93px;top:0;width:89px;height:102px;background:var(--spiral)" role="img" aria-label="Figure under a spiral galaxy"></div>
  <span class="mark light">The Lantern Guild</span>
</section>

<section class="slide" style="left:281px;top:550px">
  <h2 class="title" style="left:9px;top:5px;font-size:3.6px;color:var(--violet)">About us</h2>
  <p class="lead" style="left:9px;top:21px;width:44px;font-size:2.1px;color:var(--violet)">Lorem ipsum dolor sit amet, consectetuer adipiscing elit, sed diam nonummy nibh euismod tincidunt ut laoreet dolore magna</p>
  <p class="body" style="left:9px;top:52px;width:35px">Short notes on the plan go here with goals, dates and a clear outcome that the team will share at review. Add key facts, the budget and the people who lead each part of the work.</p>
  <p class="body" style="left:47px;top:52px;width:35px">Short notes on the plan go here with goals, dates and a clear outcome that the team will share at review. Add key facts, the budget and the people who lead each part of the work.</p>
  <div class="photo" style="left:87px;top:0;width:95px;height:102px;background:var(--cliff)" role="img" aria-label="Figure at a glowing portal in a cliff"></div>
  <span class="mark light">The Lantern Guild</span>
</section>

<section class="slide" style="left:504px;top:550px">
  <div class="photo" style="left:-50px;top:-15px;width:130px;height:130px;border-radius:50%;background:var(--dunes)" role="img" aria-label="Purple planet over dunes"></div>
  <div class="abs" style="left:0;top:0;width:30px;height:102px;background:var(--navy);clip-path:polygon(0 0,100% 0,40% 100%,0 100%);opacity:.9"></div>
  <svg class="abs" style="left:0;top:0" width="80" height="102"><circle cx="60" cy="61" r="10" fill="#3b2a8a" opacity=".8"/></svg>
  <h2 class="title light" style="left:9px;top:5px;font-size:3.6px">Benefits</h2>
  <p class="lead light" style="left:26px;top:57px;font-size:2.3px;text-align:center">Total<br>benefits</p>
  <p class="lead light" style="left:57px;top:60px;font-size:2.3px">12%</p>
  <p class="lead" style="left:83px;top:12px;width:90px;font-size:1.6px">Short lines on the purpose of the benefits below, who they help and how the team will measure the results over the year ahead with clear checks.</p>
  <h3 class="lead" style="left:83px;top:42px;font-size:2.2px;font-weight:400;color:var(--violet)">Benefits</h3>
  <ul class="abs" style="left:86px;top:47px;width:88px;font-size:1.5px;line-height:1.4">
    <li>Short notes on the first benefit and its reach.</li>
    <li style="margin-top:2px">Short notes on the second benefit.</li>
    <li style="margin-top:2px">Short notes on the third benefit, its cost and reach.</li>
    <li style="margin-top:2px">Short notes on the fourth benefit, its cost and reach.</li>
  </ul>
  <span class="mark">The Lantern Guild</span>
</section>

<section class="slide" style="left:718px;top:550px">
  <div class="abs" style="left:58px;top:0;width:45px;height:102px;background:var(--grey)"></div>
  <h2 class="title" style="left:9px;top:5px;font-size:3.6px">Sector<br>expertise</h2>
  <p class="body" style="left:9px;top:20px;font-size:2px">1.</p><p class="body" style="left:62px;top:20px;font-size:2px">2.</p><p class="body" style="left:115px;top:20px;font-size:2px">3.</p>
  <p class="body" style="left:9px;top:27px;width:40px">Short notes on this sector, the work done and the results.</p>
  <p class="body" style="left:62px;top:27px;width:40px">Short notes on this sector, the work done and the results.</p>
  <p class="body" style="left:115px;top:27px;width:40px">Short notes on this sector, the work done and the results.</p>
  <svg class="abs" style="left:0;top:0" width="182" height="102">
    <polygon points="9,47 27,47 42,62 42,102 9,102" fill="#101a33"/>
    <polygon points="62,47 80,47 95,62 95,102 62,102" fill="#c9c3de"/>
    <polygon points="115,47 133,47 148,62 148,102 115,102" fill="#101a33"/>
    <g fill="none" stroke="#fff" stroke-width=".5"><circle cx="19" cy="59" r="2"/><circle cx="72" cy="59" r="2"/><path d="M122,60 a3,3 0 0 1 6,0 Z M125,60 v3"/></g>
    <g font-size="1.5" fill="#fff"><text x="12" y="69">LOREM IPSUM</text><text x="12" y="71.2">DOLOR SIT AMET,</text><text x="12" y="73.4">CONSECTETUER</text>
    <text x="65" y="69">LOREM IPSUM</text><text x="65" y="71.2">DOLOR SIT AMET,</text><text x="65" y="73.4">CONSECTETUER</text>
    <text x="118" y="69">LOREM IPSUM</text><text x="118" y="71.2">DOLOR SIT AMET,</text><text x="118" y="73.4">CONSECTETUER</text></g>
  </svg>
</section>

<section class="slide" style="left:952px;top:550px">
  <div class="photo" style="inset:0;background:var(--dusk)" role="img" aria-label="Glowing orbit rings over a sunset shore"></div>
  <p class="lead light" style="left:10px;top:47px;width:66px;font-size:3.8px;line-height:1.2">Lorem ipsum dolor sit amet, consectetuer adipiscing elit, sed diam nonummy nibh euismod tincidunt ut laoreet dolore magna aliquam erat volutpat. Ut wisi enim ad minim veniam, quis</p>
  <span class="mark light">The Lantern Guild</span>
</section>

<!-- row 5 -->
<section class="slide" style="left:52px;top:696px">
  <div class="photo" style="inset:0;background:linear-gradient(135deg,#101a33,#3a2a7a 45%,#c86ab8 60%,#2a1f60);clip-path:polygon(0 0,100% 0,100% 22%,0 62%)" role="img" aria-label="Pink black hole in deep space"></div>
  <h2 class="title light" style="left:9px;top:5px;font-size:3.6px">Pricing</h2>
  <div class="abs dark" style="left:8px;top:12px;width:67px;height:21px;border-radius:0 3px 3px 0;opacity:.92"></div>
  <p class="body light" style="left:10px;top:13px;width:62px">Short notes on the pricing plan go here with what each level gives, the terms and the best fit for each kind of member or group.</p>
  <svg class="abs" style="left:0;top:0" width="182" height="102">
    <g stroke="#9aa0b8" stroke-width=".3"><line x1="51" y1="57" x2="51" y2="98"/><line x1="92" y1="44" x2="92" y2="98"/><line x1="133" y1="31" x2="133" y2="98"/></g>
    <g font-size="1.8" fill="#3b2a8a"><text x="10" y="61">MOST DIFFICULT</text><text x="10" y="63.4">ENTRY LEVEL</text>
    <text x="55" y="51">DIFFICULT</text><text x="55" y="53.4">MID-LEVEL</text>
    <text x="96" y="38">EASIER</text><text x="96" y="40.4">ADVANCED</text>
    <text x="137" y="25">EASIEST</text><text x="137" y="27.4">PREMIUM</text></g>
    <g font-size="2" fill="#1c2238"><text x="10" y="71">$3690</text><text x="55" y="61">$4290</text><text x="96" y="48">$4890</text><text x="137" y="35">$5490</text></g>
    <g font-size="1.5" fill="#333">
      <text x="12" y="75">• Small meetings</text><text x="12" y="77.5">• Small meetings</text><text x="12" y="80">• Small meetings</text><text x="12" y="82.5">• Small meetings</text>
      <text x="57" y="65">• Small meetings</text><text x="57" y="67.5">• Small meetings</text><text x="57" y="70">• Small meetings</text><text x="57" y="72.5">• Small meetings</text>
      <text x="98" y="52">• Small meetings</text><text x="98" y="54.5">• Small meetings</text><text x="98" y="57">• Small meetings</text><text x="98" y="59.5">• Small meetings</text>
      <text x="139" y="39">• Small meetings</text><text x="139" y="41.5">• Small meetings</text><text x="139" y="44">• Small meetings</text><text x="139" y="46.5">• Small meetings</text>
    </g>
  </svg>
  <span class="mark">The Lantern Guild</span>
</section>

<section class="slide" style="left:281px;top:696px">
  <div class="abs" style="left:66px;top:0;width:51px;height:102px;background:var(--grey)"></div>
  <div class="photo" style="left:43px;top:-50px;width:100px;height:100px;border-radius:50%;background:linear-gradient(180deg,#1a1f5a,#3a4a9a 55%,#9aa6d8 75%,#3a2e50)" role="img" aria-label="Figure on a peak above the earth"></div>
  <div class="abs" style="left:7px;top:3px;width:64px;height:13px;border-radius:0 0 5px 0;background:var(--violet)"></div>
  <h2 class="title light" style="left:10px;top:5px;font-size:3.4px">Methods of<br>differentiation</h2>
  <svg class="abs" style="left:0;top:0" width="182" height="102">
    <g fill="#101a33"><circle cx="37" cy="52" r="1.8"/><circle cx="91" cy="66" r="1.8"/><circle cx="145" cy="52" r="1.8"/></g>
    <g stroke="#fff" stroke-width=".4" fill="none"><path d="M36.2,52 l.6,.7 1.2,-1.3"/><path d="M90.2,66 l.6,.7 1.2,-1.3"/><path d="M144.2,52 l.6,.7 1.2,-1.3"/></g>
    <g font-size="1.7" fill="#3b2a8a" text-anchor="middle"><text x="37" y="57">Network of Providers</text><text x="91" y="71">Network of Providers</text><text x="145" y="57">Network of Providers</text></g>
    <g font-size="1.5" fill="#1c2238" text-anchor="middle">
      <text x="37" y="61">Short notes on this method, how it</text><text x="37" y="63">sets the team apart and why it</text><text x="37" y="65">matters.</text>
      <text x="91" y="75">Short notes on this method, how it</text><text x="91" y="77">sets the team apart and why it</text><text x="91" y="79">matters.</text>
      <text x="145" y="61">Short notes on this method, how it</text><text x="145" y="63">sets the team apart and why it</text><text x="145" y="65">matters.</text>
    </g>
  </svg>
  <span class="mark">The Lantern Guild</span>
</section>

<section class="slide" style="left:504px;top:696px">
  <div class="photo" style="inset:0;background:var(--eye)" role="img" aria-label="Close-up eye reflecting an astronaut"></div>
  <h2 class="title light" style="left:9px;top:5px;font-size:3.6px">Break</h2>
  <span class="mark light">The Lantern Guild</span>
</section>

<section class="slide" style="left:718px;top:696px">
  <div class="photo" style="inset:0;background:var(--dusk)" role="img" aria-label="Ringed planet over a misty sunset shore"></div>
  <div class="abs dark" style="left:0;top:0;width:62px;height:84px;border-radius:0 0 14px 0"></div>
  <h2 class="title light" style="left:9px;top:5px;font-size:4.8px">Thank you !</h2>
  <p class="lead light" style="left:9px;top:18px;font-size:2.2px;line-height:1.6">+010 555 0142<br>lanternguildhq.org<br>hello@lanternguildhq.org</p>
  <span class="abs light" style="right:8px;bottom:8px;font-size:3px">The Lantern Guild</span>
</section>

<section class="slide" style="left:952px;top:696px">
  <div class="photo" style="left:0;top:0;width:120px;height:102px;background:var(--deepspace)" role="img" aria-label="Pink black hole in deep space"></div>
  <div class="abs" style="left:84px;top:-5px;width:102px;height:102px;border-radius:50%;background:var(--indigo)"></div>
  <span class="abs light" style="left:9px;top:8px;font-size:3.4px;font-weight:500">The Lantern Guild</span>
  <h2 class="title light" style="left:105px;top:27px;width:62px;font-size:3.6px;line-height:1.15">Lorem ipsum dolor sit amet, consectetuer adipiscing elit, sed diam nonummy nibh</h2>
  <p class="body light" style="left:105px;top:50px;width:52px">Short notes on the plan go here with goals, dates and a clear outcome that the team will share at review. Add key facts, the budget and the people who lead each part.</p>
</section>

</main>
</body>
</html>
```